DESIGN OF STATIONERY - TORVALE MED

WE WORK IN THE FIELD OF HEALTH (IMAGING: MRI - CT ETC.).
WE WOULD LIKE TO CREATE THE ENTIRE STATIONERY DESIGN : LETTERHEAD, BUSINESS CARD, CALENDAR, INVOICES, CD HOLDER, ETC.

Target Market(s)

PERSONS UNDERTAKING HEALTH EXAMINATIONS

```html
<!DOCTYPE html>
<html lang="en">
<head>
<meta charset="utf-8">
<title>Torvale Med — Stationery</title>
<link rel="stylesheet" href="https://fonts.googleapis.com/css2?family=Montserrat:wght@400;500;600;700&family=Open+Sans:wght@400;600&display=swap">
<style>
  :root{
    --bg:#ececec;
    --paper:#f4f4f4;
    --white:#ffffff;
    --brand-blue:#1f72b8;
    --ink-blue:#1b6fb5;
    --teal:#1a9a8f;
    --text:#4a4a4a;
    --faint:#e3eaec;
    --shadow:0 2px 6px rgba(0,0,0,.12);
  }
  *{box-sizing:border-box;margin:0;padding:0}
  html,body{width:1200px;height:800px;overflow:hidden}
  body{background:var(--bg);position:relative;font-family:"Open Sans",Arial,sans-serif;color:var(--text)}
  .item{position:absolute;box-shadow:var(--shadow)}
  .paper{background:var(--paper)}
  .blue{background:var(--brand-blue)}

  /* brand lockup */
  .mark{position:absolute;display:flex;flex-direction:column;align-items:flex-start;font-family:"Montserrat",Arial,sans-serif;line-height:1}
  .mark-row{display:flex;align-items:center;gap:.25em}
  .mark-dot{width:.45em;height:.45em;border-radius:50%;background:currentColor}
  .mark-name{font-weight:600;letter-spacing:.02em;white-space:nowrap}
  .mark-tag{font-weight:500;font-size:.38em;margin-top:.25em;white-space:nowrap}
  .mark.on-light{color:var(--ink-blue)}
  .mark.on-blue{color:var(--white)}

  .tiny{font-family:"Montserrat",Arial,sans-serif;font-size:3px;line-height:4px;color:var(--text)}
  .tiny b{font-weight:700;color:#333}

  /* decorative area placeholder */
  .decor-area{position:absolute;background:linear-gradient(135deg,rgba(227,234,236,0) 0%,var(--faint) 45%,var(--faint) 100%)}

  /* square card */
  .square-card{left:146px;top:201px;width:116px;height:116px;background:var(--white)}
  /* cd holder */
  .cd-holder{left:146px;top:352px;width:116px;height:116px}
  .cd-holder .disc{position:absolute;left:11px;top:11px;width:96px;height:96px;border-radius:50%;background:var(--paper);border:1px solid #c9c9c9}
  /* business cards */
  .card-front{left:171px;top:497px;width:92px;height:53px}
  .card-back{left:171px;top:580px;width:92px;height:53px;background:var(--white)}
  .card-back .rule{position:absolute;left:49px;top:12px;width:.5px;height:29px;background:var(--teal)}
  .card-back .name{position:absolute;left:52px;top:12px;font-family:"Montserrat",sans-serif;font-size:3.2px;font-weight:700;color:var(--ink-blue);line-height:4px}
  .card-back .role{color:var(--teal);font-weight:500}
  .card-back .details{position:absolute;left:52px;top:21px;font-size:2.2px;line-height:3px}

  /* letterhead */
  .letterhead{left:316px;top:186px;width:224px;height:316px}
  .letterhead .contact{position:absolute;top:20px;font-size:3.4px;line-height:4.6px}
  .letterhead .body{position:absolute;left:22px;top:78px;width:181px;font-size:3.9px;line-height:5.9px;text-align:justify}
  .letterhead .body p{margin-bottom:6px}
  .signature{position:absolute;left:24px;top:236px;width:28px;height:22px;background:#ececec}

  /* DL envelope */
  .envelope-dl{left:317px;top:525px;width:237px;height:111px}
  .envelope-dl .address{position:absolute;left:14px;top:36px;width:62px;text-align:center;font-family:"Montserrat",sans-serif;font-size:3.6px;line-height:5px}

  /* folder */
  .folder{left:584px;top:165px;width:266px;height:340px}
  .folder .label{position:absolute;left:0;top:252px;width:98px;height:53px;background:var(--paper);padding:11px 0 0 20px;font-family:"Montserrat",sans-serif;font-size:3.8px;line-height:5px;color:#333}
  .folder .label b{display:block;margin-bottom:3px;font-weight:700}
  .folder .label .gap{display:block;height:3px}

  /* envelope with flap */
  .envelope-flap{left:600px;top:527px;width:237px;height:110px;background:var(--white)}
  .envelope-flap svg{position:absolute;left:0;top:0}

  /* screens */
  .screen-tablet{left:893px;top:193px;width:179px;height:238px;border-radius:2px}
  .screen-phone{left:892px;top:478px;width:67px;height:146px;border-radius:6px}
</style>
</head>
<body>

  <section class="item square-card" aria-label="Square compliments card">
    <div class="mark on-light" style="left:30px;top:48px;font-size:9px">
      <div class="mark-row"><span class="mark-dot"></span><span class="mark-name">Torvale Med</span></div>
      <span class="mark-tag">Health Care Diagnostic</span>
    </div>
    <div class="tiny" style="position:absolute;left:10px;top:93px"><b>COMPANY NAME</b></div>
    <div class="tiny" style="position:absolute;left:10px;top:100px;font-size:2.4px;line-height:3.2px">123 Street Hal,<br>California 5640, USA</div>
    <div class="tiny" style="position:absolute;left:48px;top:100px;font-size:2.4px;line-height:3.2px">mail@brandname.com<br>www.brandname.com</div>
  </section>

  <section class="item cd-holder blue" aria-label="CD holder">
    <div class="disc"></div>
  </section>

  <section class="item card-front blue" aria-label="Business card front">
    <div class="mark on-blue" style="left:13px;top:19px;font-size:8px">
      <div class="mark-row"><span class="mark-dot"></span><span class="mark-name">Torvale Med</span></div>
      <span class="mark-tag">Health Care Diagnostic</span>
    </div>
  </section>

  <section class="item card-back" aria-label="Business card back">
    <div class="mark on-light" style="left:7px;top:22px;font-size:5px">
      <div class="mark-row"><span class="mark-dot"></span><span class="mark-name">Torvale Med</span></div>
      <span class="mark-tag">Health Care Diagnostic</span>
    </div>
    <span class="rule"></span>
    <div class="name">NIALL R. ABERNETHY<br><span class="role">Managing Director</span></div>
    <div class="details tiny">Torvale-Med-R<br>2nd Floor 18 Larkfield<br>Crescent Glasgow G3 7PQ<br>07700 900 214<br>info@torvalemed.com<br>www.torvalemed.com</div>
  </section>

  <section class="item letterhead paper" aria-label="Letterhead">
    <div class="mark on-light" style="left:22px;top:20px;font-size:9px">
      <div class="mark-row"><span class="mark-dot"></span><span class="mark-name">Torvale Med</span></div>
      <span class="mark-tag">Health Care Diagnostic</span>
    </div>
    <div class="contact" style="left:106px">&#9742; 07700 900 214<br>&#9993; info@torvalemed.com<br>&#9679; www.torvalemed.com</div>
    <div class="contact" style="left:156px">Torvale-Med-R<br>2nd Floor 18 Larkfield<br>Crescent Glasgow G3 7PQ</div>
    <div class="body">
      <p>Dear customer,</p>
      <p>Lorem ipsum dolor sit amet, consectetur adipisicing elit, sed do eiusmod tempor incididunt ut labore et dolore magna aliqua. Ut enim ad minim veniam, quis nostrud exercitation ullamco laboris nisi ut aliquip ex ea commodo consequat. Duis aute irure dolor in reprehenderit in voluptate velit esse cillum dolore eu fugiat nulla pariatur. Excepteur sint occaecat cupidatat non proident, sunt in culpa qui officia deserunt mollit anim id est laborum.</p>
      <p>Lorem ipsum dolor sit amet, consectetur adipisicing elit, sed do eiusmod tempor incididunt ut labore et dolore magna aliqua. Ut enim ad minim veniam, quis nostrud exercitation ullamco laboris nisi ut aliquip ex ea commodo consequat. Duis aute irure dolor in reprehenderit in voluptate velit esse cillum dolore eu fugiat nulla pariatur. Excepteur sint occaecat cupidatat non proident, sunt in culpa qui officia deserunt mollit anim id est laborum.</p>
      <p>Lorem ipsum dolor sit amet, consectetur adipisicing elit, sed do eiusmod tempor incididunt ut labore et dolore magna aliqua. Ut enim ad minim veniam, quis nostrud exercitation ullamco laboris nisi ut aliquip ex ea commodo consequat. Duis aute irure dolor in reprehenderit in voluptate velit esse cillum dolore eu fugiat nulla pariatur. Excepteur sint occaecat cupidatat non proident, sunt in culpa qui officia deserunt mollit anim id est laborum.</p>
      <p>Lorem ipsum dolor sit amet, consectetur adipisicing elit, sed do eiusmod tempor incididunt ut labore et dolore magna aliqua. Ut enim ad minim veniam, quis nostrud exercitation ullamco laboris nisi ut aliquip ex ea commodo consequat. Duis aute irure dolor in reprehenderit.</p>
      <p>Yours Sincerely,</p>
    </div>
    <div class="signature" role="img" aria-label="Handwritten signature"></div>
    <div class="decor-area" style="left:146px;top:240px;width:78px;height:76px" role="img" aria-label="Faint decorative graphic in pale blue-grey"></div>
  </section>

  <section class="item envelope-dl paper" aria-label="Envelope">
    <div class="mark on-light" style="left:14px;top:16px;font-size:9px">
      <div class="mark-row"><span class="mark-dot"></span><span class="mark-name">Torvale Med</span></div>
      <span class="mark-tag">Health Care Diagnostic</span>
    </div>
    <div class="address">Torvale-Med-R<br>2nd Floor 18 Larkfield<br>Crescent Glasgow G3 7PQ</div>
    <div class="decor-area" style="left:130px;top:4px;width:104px;height:104px" role="img" aria-label="Faint decorative graphic in pale blue-grey"></div>
  </section>

  <section class="item folder blue" aria-label="Presentation folder">
    <div class="mark on-blue" style="left:67px;top:152px;font-size:17px">
      <div class="mark-row"><span class="mark-dot"></span><span class="mark-name">Torvale Med</span></div>
      <span class="mark-tag">Health Care Diagnostic</span>
    </div>
    <div class="label">
      <b>BRAND NAME .INC</b>
      47 Orchard Mews,<br>Eastfield, Leeds
      <span class="gap"></span>
      info@comapnyname.com<br>www.comapnyname.com
    </div>
  </section>

  <section class="item envelope-flap" aria-label="Envelope with flap">
    <svg width="237" height="52" viewBox="0 0 237 52" aria-hidden="true">
      <path d="M0 0 H237 L219 44 Q216 49 210 49 H27 Q21 49 18 44 Z" fill="var(--brand-blue)"/>
    </svg>
    <div class="mark on-blue" style="left:82px;top:17px;font-size:9px">
      <div class="mark-row"><span class="mark-dot"></span><span class="mark-name">Torvale Med</span></div>
      <span class="mark-tag">Health Care Diagnostic</span>
    </div>
  </section>

  <section class="item screen-tablet blue" aria-label="Tablet screen">
    <div class="mark on-blue" style="left:30px;top:102px;font-size:14px">
      <div class="mark-row"><span class="mark-dot"></span><span class="mark-name">Torvale Med</span></div>
      <span class="mark-tag">Health Care Diagnostic</span>
    </div>
  </section>

  <section class="item screen-phone blue" aria-label="Phone screen">
    <div class="mark on-blue" style="left:9px;top:68px;font-size:6px">
      <div class="mark-row"><span class="mark-dot"></span><span class="mark-name">Torvale Med</span></div>
      <span class="mark-tag">Health Care Diagnostic</span>
    </div>
  </section>

</body>
</html>
```